BRIVAN 2026 Flyer for Conference

BRIVAN needs a design for a 1-page flyer that we will hand out at an upcoming event & then later post online as a pdf. There are 3 elements which need to be on the flyer:

1) A logo. This should be prominent on the design (e.g., in the middle). The flyer should use the colors that are in that logo (e.g., for accents, design elements, and/or text; not all of these have to be used):
Dark blue: #185577
Med blue: #327C9A
Teal: #4EB1C2
Light Teal: #9EDBE6

2) The conference theme -- Oceans of Knowledge: Diving into Information Literacy -- should be at the flyer's top.

3) Finally, these six tracks should be listed below the theme and the logo (it's font size should be at least a couple sizes smaller than the size used for the theme):
- Pearls of Pedagogy: Teaching Techniques that Work
- The Depth Gauge: Measuring Instructional Impact
- Techtonic Shifts: Innovation and Educational Technology
- Captain's Log: Navigating Leadership in Library Instruction
- Swimming Together: Collaborating with Others
- The Bermuda Triangle: Exploring (Seemingly) Eternal Challenges

Font styles to use
Sans Serif

Colors
0094D4
00A9DD
6FCCEA
C7EBF8
E9F6FB

Requirements
Must have
• The 3 elements listed in the description: 1) the logo, 2) the text of the theme and 3) the text for the tracks.

```html
<!DOCTYPE html>
<html lang="en">
<head>
<meta charset="utf-8">
<title>BRIVAN 2026 – Oceans of Knowledge</title>
<link href="https://fonts.googleapis.com/css2?family=Baloo+2:wght@700;800&family=Open+Sans:wght@400;600&display=swap" rel="stylesheet">
<style>
  :root{
    --page:#f4f6f8;
    --card-top:#ffffff;
    --card-mist:#e7ebef;
    --title:#0d4f73;
    --pill-a:#10597d;
    --pill-b:#082f4c;
    --pill-text:#cdeefa;
    --sea-top:#1a7ba1;
    --sea-mid:#0f577c;
    --sea-deep:#082c49;
    --track-a:#0f5679;
    --track-b:#0a3857;
    --track-body:#9edbe6;
    --icon-bg:#f6f1e6;
    --icon-ring:#ffffff;
    --gold:#c59a45;
    --logo:#6fccea;
  }
  *{box-sizing:border-box;margin:0;padding:0}
  html,body{width:672px;height:1200px;overflow:hidden;background:var(--page)}
  .flyer{
    position:absolute;left:16px;top:187px;width:640px;height:826px;
    border-radius:26px;overflow:hidden;
    background:linear-gradient(160deg,var(--card-top) 0%,var(--card-top) 40%,var(--card-mist) 70%,var(--card-top) 100%);
    box-shadow:0 10px 28px rgba(8,44,73,.22);
  }
  .theme-title{
    position:absolute;top:22px;left:0;width:100%;text-align:center;
    font-family:"Baloo 2",sans-serif;font-weight:800;font-size:46px;line-height:1;
    color:var(--title);letter-spacing:.3px;
  }
  .theme-subtitle{
    position:absolute;left:75px;top:82px;width:490px;height:42px;border-radius:14px;
    background:linear-gradient(90deg,var(--pill-a),var(--pill-b));
    font-family:"Baloo 2",sans-serif;font-weight:800;font-size:29px;line-height:44px;
    color:var(--pill-text);text-align:center;
  }
  .hero-art{
    position:absolute;left:65px;top:140px;width:515px;height:320px;
    border-radius:48% 52% 40% 45% / 55% 55% 40% 40%;
    background:radial-gradient(ellipse at 45% 55%,#7a5a45 0%,#2f6f95 22%,#1b5f86 45%,#6fa8c6 70%,rgba(255,255,255,0) 100%);
  }
  .sea{position:absolute;left:0;top:0;width:640px;height:826px}
  .track{
    position:absolute;height:49px;width:218px;border-radius:14px;
    background:linear-gradient(90deg,var(--track-a),var(--track-b));
    box-shadow:0 3px 6px rgba(0,0,0,.25);
    padding:4px 0 0 30px;
  }
  .track.tall{height:67px}
  .track-name{font-family:"Baloo 2",sans-serif;font-weight:800;font-size:15px;line-height:18px;color:#fff}
  .track-desc{font-family:"Open Sans",sans-serif;font-size:12.5px;line-height:16px;color:var(--track-body);margin-top:2px}
  .track-icon{
    position:absolute;width:38px;height:38px;border-radius:50%;
    background:var(--icon-bg);border:2px solid var(--icon-ring);
    box-shadow:0 2px 5px rgba(0,0,0,.3);
  }
  .track-icon svg{width:100%;height:100%}
  .event-mark{
    position:absolute;left:0;top:760px;width:100%;
    display:flex;justify-content:center;align-items:center;gap:8px;
  }
  .event-dot{width:14px;height:14px;border-radius:50%;background:var(--logo)}
  .event-name{font-family:"Baloo 2",sans-serif;font-weight:800;font-size:30px;color:var(--logo);line-height:1}
</style>
</head>
<body>
<main class="flyer">
  <h1 class="theme-title">Oceans of Knowledge:</h1>
  <h2 class="theme-subtitle">Diving into Information Literacy</h2>

  <div class="hero-art" role="img" aria-label="Curling ocean wave with a whale tail wrapped around a stack of old books"></div>

  <svg class="sea" viewBox="0 0 640 826" aria-hidden="true">
    <defs>
      <linearGradient id="seaFill" x1="0" y1="0" x2="0" y2="1">
        <stop offset="0" stop-color="#1a7ba1"/>
        <stop offset=".45" stop-color="#0f577c"/>
        <stop offset="1" stop-color="#082c49"/>
      </linearGradient>
    </defs>
    <path d="M0 455 Q320 552 640 455 L640 826 L0 826 Z" fill="url(#seaFill)"/>
    <circle cx="630" cy="478" r="4" fill="#6f9fb8"/>
  </svg>

  <!-- left column -->
  <div class="track" style="left:87px;top:511px">
    <p class="track-name">Pearls of Pedagogy:</p>
    <p class="track-desc">Teaching Techniques that Work</p>
  </div>
  <div class="track-icon" style="left:71px;top:516px">
    <svg viewBox="0 0 38 38"><path d="M11 24 Q19 8 27 24 Z" fill="none" stroke="#c59a45" stroke-width="2"/><path d="M19 12 V24 M15 14 L17 24 M23 14 L21 24" stroke="#c59a45" stroke-width="1.5"/><circle cx="19" cy="27" r="2" fill="#c59a45"/></svg>
  </div>

  <div class="track tall" style="left:87px;top:577px">
    <p class="track-name">Techtonic Shifts:</p>
    <p class="track-desc">Innovation and<br>Educational Technology</p>
  </div>
  <div class="track-icon" style="left:71px;top:591px">
    <svg viewBox="0 0 38 38"><path d="M12 15 H24 V11 L29 16 L24 21 V18 H12 Z" fill="#c59a45"/><path d="M26 23 H15 V19 L10 24 L15 29 V26 H26 Z" fill="#c59a45"/></svg>
  </div>

  <div class="track tall" style="left:87px;top:658px">
    <p class="track-name">Swimming Together:</p>
    <p class="track-desc">Together: Collaborating<br>with Others</p>
  </div>
  <div class="track-icon" style="left:71px;top:672px">
    <svg viewBox="0 0 38 38"><circle cx="24" cy="13" r="2.5" fill="#c59a45"/><path d="M12 21 L19 15 L23 20" fill="none" stroke="#c59a45" stroke-width="2.2" stroke-linecap="round"/><path d="M9 25 q3-2 5 0 t5 0 t5 0 t5 0" fill="none" stroke="#c59a45" stroke-width="1.6"/><path d="M9 29 q3-2 5 0 t5 0 t5 0 t5 0" fill="none" stroke="#c59a45" stroke-width="1.6"/></svg>
  </div>

  <!-- right column -->
  <div class="track" style="left:350px;top:511px">
    <p class="track-name">The Depth Gauge:</p>
    <p class="track-desc">Measuring Instructional Impact</p>
  </div>
  <div class="track-icon" style="left:334px;top:516px">
    <svg viewBox="0 0 38 38"><circle cx="19" cy="19" r="9" fill="none" stroke="#c59a45" stroke-width="2"/><circle cx="19" cy="19" r="5" fill="none" stroke="#c59a45" stroke-width="1.4"/><path d="M19 19 L22 16" stroke="#c59a45" stroke-width="1.6"/></svg>
  </div>

  <div class="track tall" style="left:350px;top:577px">
    <p class="track-name">Captain's Log:</p>
    <p class="track-desc">Navigating Leadership in<br>Library Instruction</p>
  </div>
  <div class="track-icon" style="left:334px;top:591px">
    <svg viewBox="0 0 38 38"><path d="M12 14 H26 L24 10 H14 Z" fill="#c59a45"/><rect x="15" y="15" width="8" height="6" rx="3" fill="#c59a45"/><path d="M11 29 Q19 20 27 29 Z" fill="#c59a45"/></svg>
  </div>

  <div class="track tall" style="left:350px;top:658px">
    <p class="track-name">The Bermuda Triangle:</p>
    <p class="track-desc">Exploring (Seemingly)<br>Eternal Challenges</p>
  </div>
  <div class="track-icon" style="left:334px;top:672px">
    <svg viewBox="0 0 38 38"><path d="M12 12 L27 14 L18 27 Z" fill="none" stroke="#c59a45" stroke-width="2" stroke-linejoin="round"/><circle cx="12" cy="12" r="2" fill="#c59a45"/><circle cx="27" cy="14" r="2" fill="#c59a45"/><circle cx="18" cy="27" r="2" fill="#c59a45"/></svg>
  </div>

  <div class="event-mark">
    <span class="event-dot"></span>
    <span class="event-name">BRIVAN 2026</span>
  </div>
</main>
</body>
</html>
```